Ferncliff Capital - Website Design

We need a website design for a new commercial real estate company called Ferncliff Capital. We're effectively commercial mortgage brokers connecting real estate investors to lenders. We need a website that is simple (not busy), elegant, professional, and user-friendly. A lot of the users will be in their 50's and less tech savvy, so a stream-lined design is best. The website will serve as a portal for lenders to review new financing opportunities, as well as for real estate investors to review terms from lenders.
Updates
Just uploaded our logo.
Target Market(s)
Commercial real estate investors and lenders
Industry/Entity Type
Real Estate
Number of Pages Required
1 page
Colors
Designer to choose colors to be used in the design.
Look and feel

```html
<!DOCTYPE html>
<html lang="en">
<head>
<meta charset="utf-8">
<title>Ferncliff Capital</title>
<link href="https://fonts.googleapis.com/css2?family=Open+Sans:ital,wght@0,400;0,600;0,700;1,400&family=Roboto+Condensed:wght@400;700&display=swap" rel="stylesheet">
<style>
:root{
  --blue:#1b6fc2;
  --orange:#f5761f;
  --ink:#222;
  --body:#666;
  --muted:#999;
  --band:#efefef;
  --testi:#4a6fbd;
  --footer:#0d0d0d;
  --white:#fff;
}
*{margin:0;padding:0;box-sizing:border-box}
html,body{width:1200px;height:3273px;overflow:hidden;background:var(--white)}
body{position:relative;font-family:"Open Sans",sans-serif;color:var(--body)}
.abs{position:absolute}
.head{font-family:"Roboto Condensed",sans-serif;color:var(--ink);font-weight:400}
.center{text-align:center}

/* header */
.site-header{position:absolute;left:0;top:0;width:1200px;height:113px;background:var(--white)}
.brand{position:absolute;left:88px;top:34px;font-family:"Roboto Condensed",sans-serif;font-weight:700;font-size:30px;letter-spacing:1px;color:var(--blue);text-transform:uppercase}
.nav{position:absolute;top:44px;left:532px;display:flex;gap:0;font-size:17px;color:#333}
.nav a{color:#333;text-decoration:none;margin-right:30px}
.nav a.active{color:var(--blue)}
.search{position:absolute;left:1090px;top:43px}

/* hero */
.hero{position:absolute;left:0;top:113px;width:1200px;height:529px;background:linear-gradient(100deg,#cfc9c2 0%,#e6e0d8 35%,#d9d0c6 60%,#bfc4c8 100%)}
.hero-title{position:absolute;top:200px;width:1200px;text-align:center;font-family:"Roboto Condensed",sans-serif;font-size:52px;color:var(--white);text-shadow:0 2px 6px rgba(0,0,0,.35)}
.hero-sub{position:absolute;top:263px;width:1200px;text-align:center;font-family:"Roboto Condensed",sans-serif;font-size:33px;color:var(--white);text-shadow:0 2px 6px rgba(0,0,0,.35)}
.btn-quote{position:absolute;left:488px;top:321px;width:222px;height:48px;border-radius:24px;background:var(--orange);color:var(--white);font-family:"Roboto Condensed",sans-serif;font-size:24px;display:flex;align-items:center;justify-content:center}
.hero-arrow{position:absolute;top:387px;width:30px;height:30px;border-radius:50%;background:rgba(60,60,60,.75)}

/* welcome */
.welcome-title{position:absolute;top:722px;width:1200px;font-size:33px}
.welcome-text{position:absolute;left:175px;top:780px;width:850px;font-size:14px;line-height:26px;text-align:center}
.service{position:absolute;top:908px;width:300px;text-align:center}
.service .ring{width:106px;height:106px;border:1.5px solid #555;border-radius:50%;margin:0 auto;display:flex;align-items:center;justify-content:center}
.service h3{font-family:"Roboto Condensed",sans-serif;font-weight:400;font-size:21px;color:var(--ink);margin-top:22px}
.service p{font-size:12.5px;line-height:23px;margin-top:8px}
.service .more{font-size:12.5px;color:var(--orange);margin-top:6px}

/* commercial */
.band{position:absolute;left:0;top:1233px;width:1200px;height:487px;background:linear-gradient(120deg,#f4f4f4,#e9e9e9)}
.feature{position:absolute;left:146px;top:1311px;width:899px;height:325px;background:var(--white);box-shadow:0 4px 14px rgba(0,0,0,.15)}
.feature h2{position:absolute;left:40px;top:56px;font-family:"Roboto Condensed",sans-serif;font-weight:400;font-size:31px;color:var(--ink)}
.feature p{position:absolute;left:40px;top:108px;width:428px;font-size:13.5px;line-height:22px;text-align:justify}
.btn-more{position:absolute;left:40px;top:238px;width:108px;height:32px;border-radius:16px;background:var(--orange);color:var(--white);font-size:11px;display:flex;align-items:center;justify-content:center}
.feature-img{position:absolute;left:507px;top:0;width:392px;height:325px;background:linear-gradient(160deg,#3b4a5c 0%,#7d8fa3 45%,#c9d7e3 75%,#5d9bc0 100%)}

/* projects */
.projects-title{position:absolute;top:1826px;width:1200px;font-size:31px;text-transform:uppercase}
.project{position:absolute;top:1910px;width:311px;height:303px;background:var(--white);box-shadow:0 3px 12px rgba(0,0,0,.18);text-align:center}
.project .pic{height:166px}
.project h4{font-family:"Roboto Condensed",sans-serif;font-weight:400;font-size:17px;color:var(--ink);margin-top:18px}
.project p{font-size:11.5px;line-height:21px;margin:8px 24px 0}
.project .more{font-size:11.5px;color:var(--orange);margin-top:8px}

/* testimonial */
.testimonial{position:absolute;left:0;top:2309px;width:1200px;height:414px;background:linear-gradient(90deg,#4b72c2,#476cb8 60%,#4e70b4)}
.testimonial h2{position:absolute;top:74px;width:1200px;text-align:center;font-family:"Roboto Condensed",sans-serif;font-weight:400;font-size:31px;color:var(--white)}
.quote{position:absolute;left:220px;top:134px;width:760px;text-align:center;font-size:13px;line-height:22px;color:var(--white)}
.quote b{font-size:22px;vertical-align:-4px;margin:0 6px}
.avatar{position:absolute;left:551px;top:226px;width:98px;height:98px;border-radius:50%;border:4px solid var(--white);background:linear-gradient(#8a9bb0,#5b6a80)}
.t-name{position:absolute;top:331px;width:1200px;text-align:center;font-style:italic;font-size:13px;color:var(--white)}
.t-arrow{position:absolute;top:258px}

/* partners */
.partner{position:absolute;top:2806px;width:172px;height:100px;background:#f0f0f0;border:1px solid #e2e2e2;border-radius:3px;display:flex;align-items:center;justify-content:center}
.partner span{display:block;width:96px;height:16px;border-radius:3px;background:#cfcfcf}

/* footer */
.site-footer{position:absolute;left:0;top:2968px;width:1200px;height:305px;background:var(--footer);color:#ddd}
.footer-brand{position:absolute;left:88px;top:118px;font-family:"Roboto Condensed",sans-serif;font-weight:700;font-size:20px;color:var(--white);text-transform:uppercase;letter-spacing:.5px}
.f-head{position:absolute;top:62px;font-family:"Roboto Condensed",sans-serif;font-size:15px;color:var(--white);text-transform:uppercase}
.f-list{position:absolute;top:96px;list-style:none;font-size:12px;line-height:24px}
.f-list li::before{content:"» ";color:#ccc}
.f-contact{position:absolute;left:647px;top:96px;font-size:12px;line-height:23px;width:230px}
.social{position:absolute;top:94px;width:30px;height:30px;border-radius:50%;background:var(--white)}
.f-rule{position:absolute;left:88px;top:230px;width:1024px;height:1px;background:#2a2a2a}
.copy{position:absolute;top:258px;width:1200px;text-align:center;font-size:12px;color:#ccc}
</style>
</head>
<body>

<header class="site-header">
  <div class="brand">Ferncliff Capital</div>
  <nav class="nav">
    <a class="active">Home</a><a>About us</a><a>Services</a><a>Projects</a><a>Blog</a><a>Contact us</a>
  </nav>
  <svg class="search" width="22" height="22" viewBox="0 0 22 22"><circle cx="9" cy="9" r="6.5" fill="none" stroke="#222" stroke-width="2.6"/><line x1="14" y1="14" x2="20" y2="20" stroke="#222" stroke-width="3" stroke-linecap="round"/></svg>
</header>

<section class="hero" role="img" aria-label="Photo of a smiling young family of three on a sofa at home">
  <h1 class="hero-title">FERNCLIFF CAPITAL</h1>
  <div class="hero-sub">New commercial real estate company</div>
  <div class="btn-quote">Get A Quote</div>
  <svg class="hero-arrow" style="left:90px" viewBox="0 0 30 30"><path d="M17 9l-6 6 6 6" fill="none" stroke="#fff" stroke-width="2.5"/></svg>
  <svg class="hero-arrow" style="left:122px" viewBox="0 0 30 30"><path d="M13 9l6 6-6 6" fill="none" stroke="#fff" stroke-width="2.5"/></svg>
</section>

<h2 class="abs head center welcome-title">Welcome To Ferncliff Capital</h2>
<p class="welcome-text">It is a long established fact that a reader will be distracted by the readable content of a page when looking at its layout. The point of using Lorem Ipsum is that it has a more-or-less normal distribution of letters, as opposed to using ‘Content here, content here’, making it look like readable English</p>

<div class="service" style="left:130px">
  <div class="ring"><svg width="40" height="30" viewBox="0 0 40 30"><rect x="2" y="4" width="36" height="22" rx="2" fill="none" stroke="#1b6fc2" stroke-width="3"/><circle cx="20" cy="15" r="6" fill="#1b6fc2"/></svg></div>
  <h3>Investors</h3>
  <p>It is a long established fact that a reader<br>will be distracted by the readable</p>
  <div class="more">Learn More -&gt;</div>
</div>
<div class="service" style="left:450px">
  <div class="ring"><svg width="44" height="32" viewBox="0 0 44 32"><rect x="8" y="3" width="28" height="20" rx="1.5" fill="none" stroke="#1b6fc2" stroke-width="3"/><path d="M2 27h40" stroke="#1b6fc2" stroke-width="3.5" stroke-linecap="round"/></svg></div>
  <h3>Mortgage</h3>
  <p>It is a long established fact that a reader<br>will be distracted by the readable</p>
  <div class="more">Learn More -&gt;</div>
</div>
<div class="service" style="left:770px">
  <div class="ring"><svg width="44" height="36" viewBox="0 0 44 36" fill="#1b6fc2"><circle cx="22" cy="9" r="6"/><circle cx="9" cy="13" r="4.5"/><circle cx="35" cy="13" r="4.5"/><path d="M12 34c0-9 4-15 10-15s10 6 10 15z"/><path d="M1 32c0-7 3-12 8-12 2 0 3 1 4 2-2 3-3 6-3 10z"/><path d="M43 32c0-7-3-12-8-12-2 0-3 1-4 2 2 3 3 6 3 10z"/></svg></div>
  <h3>Lenders</h3>
  <p>It is a long established fact that a reader<br>will be distracted by the readable</p>
  <div class="more">Learn More -&gt;</div>
</div>

<section class="band">
</section>
<article class="feature">
  <h2>Commercial Real Estate</h2>
  <p>It is a long established fact that a reader will be distracted by the readable content of a page when looking at its layout. The point of using Lorem Ipsum is that it has a more-or-less normal distribution of letters, as opposed to using ‘Content here, content here’, making it look like readable English</p>
  <div class="btn-more">READ MORE</div>
  <div class="feature-img" role="img" aria-label="Photo of a business handshake over a small house model with keys"></div>
</article>

<h2 class="abs head center projects-title">Our Projects</h2>
<div class="project" style="left:105px">
  <div class="pic" role="img" aria-label="Photo of a modern two-storey house at dusk" style="background:linear-gradient(#7d9cbc,#3e4d5e 60%,#9a8f7e)"></div>
  <h4>Neque porro quisquam</h4>
  <p>It has survived not only five centuries, but also the leap into electronic typesetting,</p>
  <div class="more">Read More »</div>
</div>
<div class="project" style="left:446px">
  <div class="pic" role="img" aria-label="Photo of a brick commercial building under blue sky" style="background:linear-gradient(#5f94d2,#b5c8de 45%,#a8866e 70%,#8c8a86)"></div>
  <h4>Porro quisquam</h4>
  <p>It has survived not only five centuries, but also the leap into electronic typesetting,</p>
  <div class="more">Read More »</div>
</div>
<div class="project" style="left:788px">
  <div class="pic" role="img" aria-label="Photo of a blue suburban house with a green lawn" style="background:linear-gradient(#d6e6f2,#4a5a7a 50%,#6b9a4a)"></div>
  <h4>Neque quisquam</h4>
  <p>It has survived not only five centuries, but also the leap into electronic typesetting,</p>
  <div class="more">Read More »</div>
</div>

<section class="testimonial">
  <h2>TESTIMONIAL</h2>
  <p class="quote"><b>“</b>It is a long established fact that a reader will be distracted by the readable content of a page when looking at its layout. The point of using Lorem Ipsum is that it has a more-or-less normal distribution of letters, as opposed to using ‘Content here, content here’, making it look like readable English.<b>”</b></p>
  <svg class="t-arrow" style="left:512px" width="20" height="30" viewBox="0 0 20 30"><path d="M14 6l-9 9 9 9" fill="none" stroke="#fff" stroke-width="2.5"/></svg>
  <div class="avatar" role="img" aria-label="Portrait photo of a client"></div>
  <svg class="t-arrow" style="left:676px" width="20" height="30" viewBox="0 0 20 30"><path d="M6 6l9 9-9 9" fill="none" stroke="#fff" stroke-width="2.5"/></svg>
  <div class="t-name">Quisquam est qui</div>
</section>

<div class="partner" style="left:148px"><span></span></div>
<div class="partner" style="left:332px"><span></span></div>
<div class="partner" style="left:516px"><span></span></div>
<div class="partner" style="left:698px"><span></span></div>
<div class="partner" style="left:882px"><span></span></div>

<footer class="site-footer">
  <div class="footer-brand">Ferncliff Capital</div>
  <div class="f-head" style="left:391px">Information</div>
  <ul class="f-list" style="left:391px">
    <li>Privacy Policy</li><li>Login</li><li>Advanced Search</li><li>Contact Us</li>
  </ul>
  <div class="f-head" style="left:647px">Contact Us</div>
  <div class="f-contact">Address : 14 Alder Lane, Westmoor Hill, Canada<br>Phone : (555) 014-2290<br>Email : info@ferncliffcapital.example</div>
  <div class="f-head" style="left:935px;top:58px">Follow us out there</div>
  <div class="social" style="left:937px"></div>
  <div class="social" style="left:978px"></div>
  <div class="social" style="left:1020px"></div>
  <div class="f-rule"></div>
  <div class="copy">Copyright © 2017 All Rights Reserved</div>
</footer>

</body>
</html>
```